Oil and Gas Exploration and Production company needs a business card design

We need a business card design using our logo and colors in the logo. We want a mainstream design.

```html
<!DOCTYPE html>
<html lang="en">
<head>
<meta charset="utf-8">
<title>Halvreth Oil &amp; Gas — Business Card</title>
<link rel="stylesheet" href="https://fonts.googleapis.com/css2?family=Arimo:wght@400;700&display=swap">
<style>
  :root {
    --backdrop: #e6e3de;
    --card-white: #ffffff;
    --card-black: #080808;
    --gold: #c9962c;
    --text-light: #ffffff;
    --text-dark: #111111;
  }
  * { margin: 0; padding: 0; box-sizing: border-box; }
  html, body {
    width: 1200px; height: 902px; overflow: hidden;
    background: var(--backdrop);
    font-family: "Arimo", Arial, sans-serif;
  }
  .canvas { position: relative; width: 1200px; height: 902px; }
  .card {
    position: absolute; left: 100px; top: 165px;
    width: 1000px; height: 571px;
    background: var(--card-white);
    border-radius: 30px; overflow: hidden;
    box-shadow: 0 6px 24px rgba(0,0,0,0.18);
  }
  .card-shapes { position: absolute; inset: 0; width: 100%; height: 100%; }
  .card-shapes .panel { fill: var(--card-black); }
  .card-shapes .accent { fill: var(--gold); }

  .holder-name {
    position: absolute; left: 73px; top: 124px;
    font-size: 30px; font-weight: 700; line-height: 36px; color: var(--text-light);
  }
  .holder-role {
    position: absolute; left: 73px; top: 158px;
    font-size: 23px; line-height: 28px; color: var(--gold);
  }
  .address {
    position: absolute; left: 73px; top: 268px;
    font-size: 23px; line-height: 31px; font-style: normal; color: var(--text-light);
  }
  .contacts { position: absolute; left: 73px; top: 350px; list-style: none; }
  .contacts li {
    display: flex; align-items: center; gap: 10px;
    height: 34px; font-size: 23px; color: var(--text-light);
  }
  .contacts svg { width: 28px; height: 28px; flex: none; }
  .contacts .ring { fill: none; stroke: var(--gold); stroke-width: 1.6; }
  .contacts .glyph { fill: var(--gold); }
  .contacts .glyph-line { fill: none; stroke: var(--gold); stroke-width: 1.3; }
  .contacts .glyph-cut { fill: none; stroke: var(--card-black); stroke-width: 1.3; }

  .brand {
    position: absolute; left: 540px; top: 248px;
    display: flex; align-items: center; gap: 14px;
  }
  .brand-dot { width: 50px; height: 50px; border-radius: 50%; background: var(--text-dark); }
  .brand-name {
    font-size: 40px; font-weight: 700; color: var(--text-dark);
    letter-spacing: 0.5px; white-space: nowrap;
  }
</style>
</head>
<body>
<main class="canvas">
  <section class="card" aria-label="Halvreth Oil &amp; Gas business card">
    <svg class="card-shapes" viewBox="0 0 1000 571" preserveAspectRatio="none" aria-hidden="true">
      <path class="panel" d="M0,0 H511 Q372,285.5 511,571 H0 Z"/>
      <path class="accent" d="M514,0 Q378,285.5 514,571 L518,571 Q395,285.5 518,0 Z"/>
    </svg>

    <h1 class="holder-name">Marcus Hale</h1>
    <p class="holder-role">President &amp; CEO</p>

    <address class="address">PO Box 418, Harbour Road<br>Quay Lane, Aberdeen</address>

    <ul class="contacts">
      <li>
        <svg viewBox="0 0 28 28" aria-hidden="true">
          <circle class="ring" cx="14" cy="14" r="12"/>
          <path class="glyph" d="M8 11 Q14 7 20 11 L19 13 L17 12.5 L16.5 11 Q14 10.5 11.5 11 L11 12.5 L9 13 Z"/>
          <rect class="glyph" x="9.5" y="13.5" width="9" height="6" rx="1.2"/>
        </svg>
        (204) 555 0187
      </li>
      <li>
        <svg viewBox="0 0 28 28" aria-hidden="true">
          <circle class="ring" cx="14" cy="14" r="12"/>
          <rect class="glyph" x="8" y="10" width="12" height="8.5" rx="1"/>
          <path class="glyph-cut" d="M8.5 10.5 L14 15 L19.5 10.5"/>
        </svg>
        info@halvrethenergy.com
      </li>
      <li>
        <svg viewBox="0 0 28 28" aria-hidden="true">
          <circle class="ring" cx="14" cy="14" r="12"/>
          <circle class="glyph-line" cx="14" cy="14" r="7"/>
          <ellipse class="glyph-line" cx="14" cy="14" rx="3" ry="7"/>
          <path class="glyph-line" d="M7 14 H21 M8.2 10.5 H19.8 M8.2 17.5 H19.8"/>
        </svg>
        www.halvrethenergy.com
      </li>
    </ul>

    <div class="brand">
      <span class="brand-dot" aria-hidden="true"></span>
      <span class="brand-name">Halvreth Oil &amp; Gas</span>
    </div>
  </section>
</main>
</body>
</html>
```